Ferncliff Capital - Website Design

We need a website design for a new commercial real estate company called Ferncliff Capital. We're effectively commercial mortgage brokers connecting real estate investors to lenders. We need a website that is simple (not busy), elegant, professional, and user-friendly. A lot of the users will be in their 50's and less tech savvy, so a stream-lined design is best. The website will serve as a portal for lenders to review new financing opportunities, as well as for real estate investors to review terms from lenders.
Updates
Just uploaded our logo.
Target Market(s)
Commercial real estate investors and lenders
Industry/Entity Type
Real Estate
Number of Pages Required
1 page
Colors
Designer to choose colors to be used in the design.
Look and feel

```html
<!DOCTYPE html>
<html lang="en">
<head>
<meta charset="utf-8">
<title>Ferncliff Capital</title>
<link rel="stylesheet" href="https://fonts.googleapis.com/css2?family=Arvo:wght@400;700&family=Noto+Serif:wght@400;700&display=swap">
<style>
:root{
  --blue:#1f9ad6;
  --blue-dark:#1784bb;
  --green:#6cae2a;
  --green-dark:#5a9620;
  --ink:#222;
  --text:#555;
  --muted:#888;
  --line:#e2e2e2;
  --white:#fff;
  --footer:#1d1d1d;
  --red:#e0262a;
  --amber:#f2b84b;
}
*{box-sizing:border-box;margin:0;padding:0}
html,body{width:1200px;height:3704px;overflow:hidden}
body{position:relative;background:var(--white);font-family:"Noto Serif",Georgia,serif;color:var(--text)}
.abs{position:absolute}
h2.section-title{position:absolute;font-family:"Arvo",Georgia,serif;font-weight:700;font-size:29px;color:var(--ink)}
.center{left:0;width:1200px;text-align:center}

/* hero */
.hero{left:0;top:0;width:1200px;height:563px;background:linear-gradient(180deg,#5a4c44 0%,#8f8177 35%,#cfc8c1 70%,#e9e6e3 100%)}
.hero-shade{left:0;top:0;width:1200px;height:200px;background:linear-gradient(180deg,rgba(0,0,0,.45),rgba(0,0,0,0))}
.brand{left:99px;top:40px;display:flex;align-items:center;gap:12px}
.brand-mark{width:44px;height:44px;border:3px solid var(--white)}
.brand-name{font-family:"Arvo",serif;font-weight:700;font-size:28px;color:var(--white)}
.nav{right:99px;top:52px;display:flex;align-items:center;gap:30px;font-size:14px;color:var(--white)}
.nav .caret{font-size:10px}
.btn-book{border:2px solid var(--white);border-radius:20px;padding:9px 22px;font-weight:700;font-size:13px}
.hero-title{top:262px;font-family:"Arvo",serif;font-weight:700;font-size:52px;color:var(--white);text-shadow:0 2px 6px rgba(0,0,0,.35)}
.hero-sub{top:333px;font-size:14px;color:#f4f0ec}
.hero-arrow{top:296px;width:24px;height:30px;background:rgba(0,0,0,.45);color:var(--white);font-size:16px;display:flex;align-items:center;justify-content:center}

.quote{left:131px;top:486px;width:941px;height:144px;display:flex;box-shadow:0 4px 12px rgba(0,0,0,.12)}
.quote-form{flex:1;background:var(--white);padding:32px 34px 0}
.quote-form h3{font-weight:400;font-size:19px;color:var(--ink);margin-bottom:14px}
.quote-fields{display:flex;gap:8px}
.quote-field{width:164px;height:33px;border:1px solid var(--line);font-size:11px;color:var(--muted);padding:0 10px;display:flex;align-items:center;justify-content:space-between}
.quote-apply{width:220px;background:var(--blue);color:var(--white);font-family:"Arvo",serif;font-weight:700;font-size:24px;display:flex;align-items:center;justify-content:center;clip-path:polygon(0 0,100% 0,100% 100%,0 100%,12% 50%)}

/* featured */
.slider-btns{left:901px;top:704px;display:flex;gap:4px}
.slider-btn{width:98px;height:34px;font-size:13px;display:flex;align-items:center;justify-content:center;border:1px solid var(--green)}
.slider-btn.prev{color:var(--green);background:var(--white)}
.slider-btn.next{color:var(--white);background:var(--green)}
.card{top:768px;width:321px;height:454px;border:1px solid var(--line);background:var(--white)}
.card-photo{position:absolute;left:8px;top:12px;width:303px;height:232px}
.offer{position:absolute;left:22px;top:148px;width:82px;height:82px;border-radius:50%;border:4px solid var(--white);color:var(--white);font-family:"Arvo",serif;font-weight:700;font-size:20px;text-align:center;line-height:1.05;padding-top:17px}
.offer small{display:block;font-size:14px;font-weight:400}
.card-title{position:absolute;left:8px;top:266px;font-size:14px;color:var(--ink)}
.card-text{position:absolute;left:8px;top:292px;width:300px;font-size:12px;line-height:20px;color:var(--muted)}
.card-rule{position:absolute;left:0;top:345px;width:100%;border-top:1px solid var(--line)}
.features{position:absolute;left:8px;top:362px;display:grid;grid-template-columns:130px 150px;row-gap:24px;font-size:12px;color:var(--text)}
.features span{display:flex;align-items:center;gap:10px}

/* stats */
.stats{left:0;top:1304px;width:1200px;height:234px;background:linear-gradient(90deg,#5d5146,#8c7b6a 45%,#a4a7aa 75%,#c7ccd0)}
.stats-dim{left:0;top:1304px;width:1200px;height:234px;background:rgba(0,0,0,.3)}
.stat{top:1380px;color:var(--white)}
.stat-num{display:flex;align-items:center;gap:12px;font-family:"Arvo",serif;font-size:38px}
.stat-label{font-size:16px;margin-top:4px;padding-left:2px}

/* about */
.about-text{left:180px;top:1668px;width:840px;text-align:center;font-size:12.5px;line-height:30px;color:var(--text)}
.frame{top:1783px;height:402px;background:#f5f5f5;border:6px solid #eaeaea;box-shadow:0 3px 8px rgba(0,0,0,.25)}
.frame-fill{position:absolute;inset:8px}
.clip{position:absolute;top:-14px;width:14px;height:22px;background:#333;border-radius:2px}

/* blog */
.blog{left:0;top:2267px;width:1200px;height:476px;background:var(--blue)}
.blog .section-title{color:var(--white)}
.post{top:2432px;width:318px;height:205px;background:var(--white);box-shadow:0 4px 10px rgba(0,0,0,.25)}
.post-photo{position:absolute;left:18px;top:68px;width:128px;height:108px}
.post-date{position:absolute;left:76px;top:157px;background:rgba(0,0,0,.75);color:var(--white);font-size:9px;padding:2px 5px}
.post-title{position:absolute;left:160px;top:64px;font-size:12px;color:var(--ink)}
.post-meta{position:absolute;left:160px;top:88px;font-size:10px;color:var(--muted)}
.post-meta b{color:var(--green)}
.post-text{position:absolute;left:160px;top:108px;width:145px;font-size:10.5px;line-height:17px;color:var(--muted)}
.pin{position:absolute;top:-6px;width:30px;height:30px;border-radius:50%;background:var(--red);box-shadow:0 2px 3px rgba(0,0,0,.3)}
.read-more{top:2656px;font-size:13px;color:var(--white);text-decoration:underline}

/* testimonial */
.t-arrow{top:2960px;font-size:26px;color:var(--ink)}
.t-name{left:141px;top:2922px;font-size:15px;color:var(--ink)}
.t-text{left:141px;top:2962px;width:720px;font-size:12px;line-height:25px;font-style:italic;color:var(--muted)}
.t-more{left:141px;top:3048px;font-size:12px;color:var(--green);text-decoration:underline}
.t-photo{left:894px;top:2884px;width:205px;height:205px;border-radius:50%;border:6px solid #eee;background:radial-gradient(circle at 50% 40%,#d9d2cc,#aeb3b7 70%)}

/* contact band */
.contact{left:0;top:3150px;width:1200px;height:104px;background:var(--green);color:var(--white)}
.contact-col{top:3150px;height:104px;display:flex;flex-direction:column;justify-content:center}
.contact-div{top:3150px;width:1px;height:104px;background:rgba(255,255,255,.3)}
.contact-label{font-size:15px;margin-bottom:12px}
.contact-value{display:flex;align-items:center;gap:12px;font-size:16px}

/* form */
.input{height:43px;border:1px solid #cfcfcf;font-size:10px;color:#aaa;padding:14px 12px}
.btn{top:3545px;width:94px;height:38px;font-size:13px;font-weight:700;display:flex;align-items:center;justify-content:center}
.btn.send{left:847px;background:var(--blue);color:var(--white)}
.btn.clear{left:958px;border:2px solid var(--blue);color:var(--blue);background:var(--white)}

.footer{left:0;top:3649px;width:1200px;height:55px;background:var(--footer);color:var(--white);font-size:12px}
.footer-copy{left:99px;top:20px}
.social{right:99px;top:10px;display:flex;gap:10px}
.social span{width:34px;height:34px;border-radius:50%;border:2px solid var(--white)}
</style>
</head>
<body>

<!-- HERO -->
<div class="abs hero" role="img" aria-label="Photo of a bright modern living room with a fireplace and white sofa"></div>
<div class="abs hero-shade"></div>
<div class="abs brand"><span class="brand-mark"></span><span class="brand-name">Ferncliff Capital</span></div>
<nav class="abs nav">
  <span>Home</span><span>About us</span><span>Property <span class="caret">&#9660;</span></span><span>Blog</span><span>Contact us</span><span>Sign in</span><span class="btn-book">BOOK ONLINE</span>
</nav>
<div class="abs center hero-title">Ferncliff Capital</div>
<div class="abs center hero-sub">Smart commercial financing connecting investors with trusted lenders nationwide</div>
<div class="abs hero-arrow" style="left:0">&#8249;</div>
<div class="abs hero-arrow" style="right:0">&#8250;</div>

<div class="abs quote">
  <div class="quote-form">
    <h3>GET YOUR PROPERTY LOAN QUOTE NOW</h3>
    <div class="quote-fields">
      <div class="quote-field">Name
        <svg width="11" height="11" viewBox="0 0 12 12"><circle cx="6" cy="3.5" r="3" fill="#777"/><path d="M0 12c0-4 12-4 12 0z" fill="#777"/></svg></div>
      <div class="quote-field">Email
        <svg width="12" height="9" viewBox="0 0 12 9"><rect width="12" height="9" fill="#777"/><path d="M0 0l6 5 6-5" stroke="#fff" fill="none"/></svg></div>
      <div class="quote-field">Mobile<span>&#8693;</span></div>
      <div class="quote-field">City<span>&#9662;</span></div>
    </div>
  </div>
  <div class="quote-apply">Apply Now</div>
</div>

<!-- FEATURED -->
<h2 class="section-title" style="left:99px;top:698px">Featured Properties</h2>
<div class="abs slider-btns"><div class="slider-btn prev">&#10229; Prev</div><div class="slider-btn next">Next &#10230;</div></div>

<div class="abs card" style="left:99px">
  <div class="card-photo" role="img" aria-label="Photo of a brick commercial building under blue sky" style="background:linear-gradient(180deg,#3b74c4,#9cc0e6 50%,#b89a7e 80%,#8a7a6c)"></div>
  <div class="offer" style="background:var(--green)">$38.9<small>Offer</small></div>
  <div class="card-title">INVENTORE VERITATIS ET QUAS</div>
  <div class="card-text">Modern retail space with ample parking in a busy district close to...</div>
  <div class="card-rule"></div>
  <div class="features"><span>&#9636; 277 Sq ft</span><span>&#9635; 4 Bathrooms</span><span>&#9636; 3 Bedrooms</span><span>&#9635; 2 Kitchen</span></div>
</div>
<div class="abs card" style="left:440px">
  <div class="card-photo" role="img" aria-label="Photo of a modern glass apartment tower at dusk" style="background:linear-gradient(180deg,#1f56b8,#5d8fd8 45%,#6b7a6a 80%,#4d5a48)"></div>
  <div class="offer" style="background:var(--amber)">$38.9<small>Offer</small></div>
  <div class="card-title">INVENTORE VERITATIS ET QUAS</div>
  <div class="card-text">Glass tower offices with flexible floor plans in a growing business...</div>
  <div class="card-rule"></div>
  <div class="features"><span>&#9636; 277 Sq ft</span><span>&#9635; 4 Bathrooms</span><span>&#9636; 3 Bedrooms</span><span>&#9635; 2 Kitchen</span></div>
</div>
<div class="abs card" style="left:780px">
  <div class="card-photo" role="img" aria-label="Photo of white townhouses on a residential street" style="background:linear-gradient(180deg,#5d86c8,#c7d4e6 45%,#e7e2dc 75%,#9a9a92)"></div>
  <div class="offer" style="background:var(--red)">$38.9<small>Offer</small></div>
  <div class="card-title">INVENTORE VERITATIS ET QUAS</div>
  <div class="card-text">Townhouse complex with steady rental income and low vacancy rates...</div>
  <div class="card-rule"></div>
  <div class="features"><span>&#9636; 277 Sq ft</span><span>&#9635; 4 Bathrooms</span><span>&#9636; 3 Bedrooms</span><span>&#9635; 2 Kitchen</span></div>
</div>

<!-- STATS -->
<div class="abs stats" role="img" aria-label="Photo of an open interior with a wooden staircase and large windows"></div>
<div class="abs stats-dim"></div>
<div class="abs stat" style="left:106px"><div class="stat-num">
  <svg width="40" height="32" viewBox="0 0 40 32" fill="#fff"><circle cx="20" cy="8" r="7"/><circle cx="7" cy="11" r="5"/><circle cx="33" cy="11" r="5"/><path d="M8 32c0-12 24-12 24 0z"/><path d="M0 28c0-8 10-9 12-6l-2 6z"/><path d="M40 28c0-8-10-9-12-6l2 6z"/></svg>533+</div><div class="stat-label">Happy Clients</div></div>
<div class="abs stat" style="left:383px"><div class="stat-num">
  <svg width="30" height="32" viewBox="0 0 30 32" fill="none" stroke="#fff" stroke-width="2.5"><path d="M2 14h6v16H2zM8 15l7-13c3 0 4 2 3 6l-1 5h9c2 0 3 2 2 4l-3 11c-1 2-2 2-4 2H8"/></svg>356</div><div class="stat-label">Projects Done</div></div>
<div class="abs stat" style="left:637px"><div class="stat-num">
  <svg width="26" height="34" viewBox="0 0 26 34" fill="#fff"><path d="M0 0h26v34H0z"/><g fill="#6a5d52"><rect x="4" y="4" width="5" height="5"/><rect x="11" y="4" width="5" height="5"/><rect x="18" y="4" width="5" height="5"/><rect x="4" y="12" width="5" height="5"/><rect x="11" y="12" width="5" height="5"/><rect x="18" y="12" width="5" height="5"/><rect x="10" y="24" width="7" height="10"/></g></svg>500+</div><div class="stat-label">Great Apartments</div></div>
<div class="abs stat" style="left:904px"><div class="stat-num">
  <svg width="32" height="32" viewBox="0 0 32 32" fill="#fff"><path d="M8 2h16v10a8 8 0 0 1-16 0z"/><path d="M8 5H2c0 7 4 9 7 9M24 5h6c0 7-4 9-7 9" fill="none" stroke="#fff" stroke-width="2.5"/><rect x="14" y="19" width="4" height="7"/><rect x="9" y="26" width="14" height="5"/></svg>213</div><div class="stat-label">Winning Awards</div></div>

<!-- ABOUT -->
<h2 class="section-title center" style="top:1612px">About us</h2>
<p class="abs about-text">We connect commercial real estate investors with lenders who understand their goals. Our team reviews every opportunity with care, presents clear terms and guides each client from first inquiry to closing, so that owners and lenders alike can make confident decisions without the usual delays, confusion or paperwork.</p>
<div class="abs frame" style="left:136px;width:437px">
  <span class="clip" style="left:30px"></span><span class="clip" style="left:140px"></span><span class="clip" style="left:270px"></span><span class="clip" style="left:390px"></span>
  <div class="frame-fill" role="img" aria-label="Photo of a lit shopping plaza at twilight" style="background:linear-gradient(180deg,#1e3f8f,#4a73c2 45%,#c7a778 70%,#7c7770)"></div>
</div>
<div class="abs frame" style="left:615px;width:452px">
  <span class="clip" style="left:30px"></span><span class="clip" style="left:150px"></span><span class="clip" style="left:280px"></span><span class="clip" style="left:400px"></span>
  <div class="frame-fill" role="img" aria-label="Photo looking up at glass skyscrapers with an airplane overhead" style="background:linear-gradient(135deg,#6b6f78,#cfd8e2 45%,#e6eef5 60%,#7d858f)"></div>
</div>

<!-- BLOG -->
<div class="abs blog"></div>
<h2 class="section-title center" style="top:2333px;color:var(--white)">Latest Blog posts</h2>

<div class="abs post" style="left:89px;transform:rotate(-1.5deg)">
  <span class="pin" style="left:150px"></span>
  <div class="post-photo" role="img" aria-label="Photo of a house lit at night" style="background:linear-gradient(180deg,#2b2f3a,#6d5a45 60%,#3b3b36)"></div>
  <span class="post-date">Nov 10,2017</span>
  <div class="post-title">PLEASURE AND PRAISING</div>
  <div class="post-meta"><b>&#9644;</b> - 3 beds &nbsp;<b>&#9644;</b> - 1 Room</div>
  <div class="post-text">Five questions to ask before signing your next commercial loan...</div>
</div>
<div class="abs post" style="left:432px;transform:rotate(1deg)">
  <span class="pin" style="left:150px"></span>
  <div class="post-photo" role="img" aria-label="Photo of a white office building" style="background:linear-gradient(180deg,#5a86c6,#d8d4cc 55%,#8a8a80)"></div>
  <span class="post-date">Nov 10,2017</span>
  <div class="post-title">TROUBLES CEPTURI THEY</div>
  <div class="post-meta"><b>&#9644;</b> - 3 beds &nbsp;<b>&#9644;</b> - 1 Room</div>
  <div class="post-text">How lenders weigh location, tenancy and cash flow in reviews...</div>
</div>
<div class="abs post" style="left:778px;transform:rotate(-1deg)">
  <span class="pin" style="left:150px"></span>
  <div class="post-photo" role="img" aria-label="Photo of a modern atrium interior" style="background:linear-gradient(180deg,#7e9cc0,#c9d3d8 50%,#6f8a6c)"></div>
  <span class="post-date">Nov 10,2017</span>
  <div class="post-title">ACCUSANTIUM OF THEM</div>
  <div class="post-meta"><b>&#9644;</b> - 3 beds &nbsp;<b>&#9644;</b> - 1 Room</div>
  <div class="post-text">Refinancing in a shifting market: timing and terms explained...</div>
</div>
<span class="abs read-more" style="left:224px">Read More</span>
<span class="abs read-more" style="left:580px">Read More</span>
<span class="abs read-more" style="left:936px">Read More</span>

<!-- TESTIMONIAL -->
<h2 class="section-title center" style="top:2830px">What Our Agents Say</h2>
<span class="abs t-arrow" style="left:50px">&#8249;</span>
<span class="abs t-arrow" style="left:1134px">&#8250;</span>
<svg class="abs" style="left:98px;top:2880px" width="20" height="16" viewBox="0 0 20 16" fill="var(--blue)"><path d="M0 16V9C0 4 3 1 8 0v3C5 4 4 6 4 8h4v8zM12 16V9c0-5 3-8 8-9v3c-3 1-4 3-4 5h4v8z"/></svg>
<div class="abs t-name">GRAECE MALUISSET ET MEA</div>
<p class="abs t-text">Working with this team made every step of financing clear and calm. They matched our project with lenders who understood it, explained each term in plain language and kept us informed from the first call until the papers were signed, which saved us weeks of effort and plenty of stress along the way.</p>
<span class="abs t-more">Read More</span>
<div class="abs t-photo" role="img" aria-label="Portrait photo of a smiling agent"></div>

<!-- CONTACT BAND -->
<div class="abs contact"></div>
<div class="abs contact-col" style="left:104px;color:var(--white)">
  <div class="contact-value">
    <svg width="28" height="24" viewBox="0 0 28 24" fill="#fff"><path d="M14 0l14 12h-4v12h-7v-8h-6v8H4V12H0z"/></svg>
    <span style="line-height:26px">482 Harbor Lane Millbrook<br>VA , 20190</span>
  </div>
</div>
<div class="abs contact-div" style="left:459px"></div>
<div class="abs contact-col" style="left:537px;color:var(--white)">
  <div class="contact-label">Email us :</div>
  <div class="contact-value"><svg width="18" height="14" viewBox="0 0 18 14"><rect x="1" y="1" width="16" height="12" fill="none" stroke="#fff" stroke-width="2"/><path d="M1 1l8 7 8-7" fill="none" stroke="#fff" stroke-width="2"/></svg>info @ ferncliffcapital.example</div>
</div>
<div class="abs contact-div" style="left:914px"></div>
<div class="abs contact-col" style="left:937px;color:var(--white)">
  <div class="contact-label">Call Us</div>
  <div class="contact-value"><svg width="14" height="22" viewBox="0 0 14 22"><rect width="14" height="22" rx="2" fill="#fff"/><rect x="2" y="3" width="10" height="13" fill="var(--green)"/></svg>1800 . 555 . 0142</div>
</div>

<!-- FORM -->
<div class="abs input" style="left:160px;top:3308px;width:280px">NAME</div>
<div class="abs input" style="left:469px;top:3308px;width:277px">PHONE</div>
<div class="abs input" style="left:770px;top:3308px;width:282px">EMAIL</div>
<div class="abs input" style="left:160px;top:3375px;width:892px;height:146px">MESSAGE</div>
<div class="abs btn send">SEND</div>
<div class="abs btn clear">CLEAR</div>

<!-- FOOTER -->
<div class="abs footer">
  <span class="abs footer-copy">&copy; copyright 2017 Ferncliff Capital. All Rights Reserved &nbsp;|&nbsp; Privacy policy</span>
  <div class="abs social"><span></span><span></span><span></span><span></span></div>
</div>

</body>
</html>
```